Label design for an exciting new Vodka brand

We need a label design for a dynamic new Vodka brand called 'Pale lantern drift Vodka'. It is a crisp and versatile liquid with a clean and smooth finish. It should appeal to 21-39 year olds, with a slight female skew. Colours, fonts and styles should be modern and relatively neutral - take inspiration from the brand pictures attached.

Target Market(s)

21-39 year olds, both male and female, but with a slight female skew

```html
<!DOCTYPE html>
<html lang="en">
<head>
<meta charset="utf-8">
<title>Pale lantern drift Vodka — Label</title>
<link rel="stylesheet" href="https://fonts.googleapis.com/css2?family=Playfair+Display:wght@700&family=Allura&family=Montserrat:wght@300&display=swap">
<style>
  :root {
    --page: #ffffff;
    --label-sky: #93a9f0;
    --foil-gold: #fbb40c;
    --script-white: #ffffff;
  }
  html, body {
    margin: 0;
    padding: 0;
    width: 1200px;
    height: 1200px;
    overflow: hidden;
    background: var(--page);
  }
  .canvas {
    width: 1200px;
    height: 1200px;
    display: flex;
    align-items: center;
    justify-content: center;
  }
  .label {
    display: block;
    width: 748px;
    height: 1000px;
  }
  .label__ground { fill: var(--label-sky); }
  .label__title {
    font-family: "Playfair Display", Georgia, serif;
    font-weight: 700;
    fill: var(--foil-gold);
  }
  .label__script {
    font-family: "Allura", cursive;
    fill: var(--script-white);
  }
  .label__spirit {
    font-family: "Montserrat", Arial, sans-serif;
    font-weight: 300;
    fill: var(--script-white);
  }
</style>
</head>
<body>
  <main class="canvas">
    <svg class="label" viewBox="0 0 630 842" xmlns="http://www.w3.org/2000/svg" aria-label="Pale lantern drift Vodka label">
      <rect class="label__ground" x="0" y="0" width="630" height="842"/>

      <text class="label__title" x="104" y="255" font-size="150" textLength="300" lengthAdjust="spacingAndGlyphs">Pale</text>
      <text class="label__title" x="128" y="375" font-size="110" textLength="400" lengthAdjust="spacingAndGlyphs">lantern</text>
      <text class="label__script" x="240" y="468" font-size="120" textLength="250" lengthAdjust="spacingAndGlyphs">Drift</text>

      <text class="label__spirit" x="80" y="612" font-size="76" textLength="476" lengthAdjust="spacing">VODKA</text>
    </svg>
  </main>
</body>
</html>
```